Podiatry clinic requires a modern revamp and editing of existing website.

I would like a fresh new look and updated information for my current business website. An easy to navigate site with prominent address and phone number for call to action. We are a podiatry clinic that focuses on general and sports podiatry.
I would like 4 pages; including Home page, About Us, Services & Contact.
www.brambleridgepodiatry.net

Target Market(s)

Active working professionals.

Industry/Entity Type

Medical

Coding

Coded - Design and coding required

Number of Pages Required

4 page

Font styles to use
Sans Serif

Colors
6b449b

Requirements
Must have
• A modern look with logo and active images; clean and uncluttered. Visible phone number and address for call to action.
• 4 pages - Home, About Us, Services, Contact.
• Home page - update address & service logos.
• About Us - update of personal information.
• Services - Revamp of existing page.
• Contact page to include Google map, email & phone number.
Nice to have
• Ability to add content easily; eg. a blog or adding video onto Home page.
• Link to Facebook page.

```html
<!DOCTYPE html>
<html lang="en">
<head>
<meta charset="utf-8">
<title>Bramble Ridge Podiatry</title>
<link href="https://fonts.googleapis.com/css2?family=Raleway:wght@400;500;600;700&family=Lato:wght@400;700&display=swap" rel="stylesheet">
<style>
:root{
  --purple:#5b3a8e;
  --orange:#f36f21;
  --ink:#222222;
  --text:#333333;
  --paper:#f6f5f3;
  --line:#d8d8d8;
  --footer:#1f1f1f;
  --footer-deep:#141414;
  --placeholder:#cfcfcf;
  --white:#ffffff;
}
*{margin:0;padding:0;box-sizing:border-box}
html,body{width:1200px;height:2586px;overflow:hidden}
body{position:relative;background:var(--white);font-family:"Lato",Arial,sans-serif;color:var(--text)}
.abs{position:absolute}
.section-title{position:absolute;left:0;width:1200px;text-align:center;font-family:"Raleway",sans-serif;font-weight:400;font-size:32px;color:var(--ink);letter-spacing:.5px}
.section-title span{color:var(--orange)}
.title-rule{position:absolute;left:407px;width:469px;height:1px;background:var(--line)}

/* header */
.site-header{left:0;top:0;width:1200px;height:116px;background:var(--white);border-bottom:1px solid #e6e6e6}
.brand{left:100px;top:30px;display:flex;align-items:center;gap:10px;font-family:"Raleway",sans-serif;font-weight:700;font-size:22px;color:var(--purple);line-height:1.1;width:180px}
.brand-dot{width:16px;height:16px;border-radius:50%;background:var(--orange);flex:none}
.topbar-phone{left:624px;top:0;width:200px;height:31px;background:var(--purple);border-radius:0 0 0 24px;color:#fff;font-size:14px;font-weight:700;display:flex;align-items:center;justify-content:center;gap:10px}
.topbar-email{left:810px;top:0;width:285px;height:31px;background:var(--orange);border-radius:0 0 24px 24px;color:#fff;font-size:14px;font-weight:700;display:flex;align-items:center;justify-content:center;gap:10px}
.main-nav a{position:absolute;top:68px;font-family:"Raleway",sans-serif;font-size:14px;color:var(--ink);text-decoration:none;transform:translateX(-50%);letter-spacing:.3px}
.main-nav a.active{color:var(--orange)}
.nav-underline{left:490px;top:110px;width:54px;height:4px;background:var(--orange)}
.nav-sep{top:68px;width:1px;height:20px;background:var(--line)}

/* hero */
.hero{left:0;top:116px;width:1200px;height:513px;background:linear-gradient(180deg,#8ec6ea 0%,#cfe6f4 55%,#6e6a66 78%,#3a3836 100%)}
.hero-title{left:100px;top:310px;font-family:"Raleway",sans-serif;font-weight:600;font-size:30px;line-height:43px;color:var(--ink)}
.btn{position:absolute;background:var(--orange);color:#fff;font-size:13px;display:flex;align-items:center;justify-content:center;letter-spacing:.5px}

/* about */
.about{left:0;top:629px;width:1200px;height:400px;background:var(--paper)}
.portrait{left:98px;top:760px;width:216px;height:217px;background:linear-gradient(160deg,#9a8a7a,#5a4a42);box-shadow:3px 3px 6px rgba(0,0,0,.25);border:3px solid #fff}
.about-role{left:341px;top:770px;font-family:"Raleway",sans-serif;font-size:20px;color:var(--ink)}
.about-name{left:341px;top:808px;font-size:14px;font-weight:700;color:var(--ink)}
.about-bio{left:341px;top:838px;width:760px;font-size:12.5px;line-height:23px;color:var(--text)}

/* services */
.services{left:0;top:1029px;width:1200px;height:635px;background:linear-gradient(90deg,#e9e4df 0%,#f4f1ee 45%,#e6e0da 100%)}
.services-intro{left:120px;top:1148px;width:960px;text-align:center;font-size:12.5px;line-height:21px;color:var(--ink)}
.tab{top:1221px;height:41px;font-family:"Raleway",sans-serif;font-size:16px;display:flex;align-items:center;justify-content:center}
.tab.on{left:346px;width:247px;background:var(--orange);color:#fff}
.tab.off{left:595px;width:257px;background:#d9d9d9;color:#444}
.card-photo{top:1307px;width:227px;height:151px;border:3px solid #fff;box-shadow:0 2px 6px rgba(0,0,0,.2)}
.card-title{top:1484px;width:227px;text-align:center;font-family:"Raleway",sans-serif;font-size:17px;line-height:21px;color:var(--ink)}
.card-text{top:1534px;width:227px;text-align:center;font-size:12.5px;line-height:19px;color:var(--ink);height:57px;overflow:hidden}
.card-plus{top:1601px;width:22px;height:22px;background:var(--orange);color:#fff;font-weight:700;font-size:18px;line-height:22px;text-align:center}
.slider-arrow{color:#b5b5b5;font-size:30px;font-family:"Raleway",sans-serif}

/* testimonials */
.testimonial{top:1812px;width:488px;height:145px;background:#ececec;border-radius:10px}
.testimonial h3{position:absolute;left:18px;top:18px;font-size:14px;font-weight:700;color:var(--orange)}
.testimonial p{position:absolute;left:18px;top:40px;width:340px;font-size:12.5px;line-height:19px;color:var(--text)}
.quote-mark{position:absolute;right:24px;top:10px;font-family:"Raleway",sans-serif;font-size:150px;line-height:1;color:#fff}
.tail{top:1957px;width:0;height:0;border-left:22px solid transparent;border-right:22px solid transparent;border-top:22px solid #ececec}
.avatar{top:1924px;width:92px;height:92px;border-radius:50%;border:3px solid var(--orange);background:linear-gradient(160deg,#cdb7a6,#8e7a6c)}
.client-name{top:1975px;font-family:"Raleway",sans-serif;font-weight:700;font-size:14px;color:var(--ink)}
.client-name .stars{color:var(--orange);letter-spacing:2px;margin-left:8px}
.round-arrow{width:30px;height:30px;border-radius:50%;border:1px solid #ccc;color:#999;font-size:20px;display:flex;align-items:center;justify-content:center}

/* partners */
.partners{left:0;top:2060px;width:1200px;height:198px;background:#ececec}
.badge{top:2103px;width:197px;height:112px;background:#fff;box-shadow:0 1px 3px rgba(0,0,0,.12);display:flex;align-items:center;justify-content:center}
.badge i{display:block;width:120px;height:46px;border-radius:6px}
.accent-rule{left:0;top:2258px;width:1200px;height:5px;background:var(--orange)}

/* footer */
.site-footer{left:0;top:2263px;width:1200px;height:280px;background:var(--footer)}
.footer-heading{top:2310px;font-family:"Raleway",sans-serif;font-weight:700;font-size:15px;color:#fff;letter-spacing:.5px}
.footer-heading::after{content:"";position:absolute;left:0;top:24px;width:32px;height:2px;background:var(--orange)}
.quick-links{left:102px;top:2341px;list-style:none}
.quick-links li{font-size:12px;color:#ddd;line-height:34px}
.quick-links li::before{content:"» ";color:var(--orange)}
.quick-links li.on{color:var(--orange)}
.footer-sep{top:2305px;width:1px;height:200px;background:#3a3a3a}
.contact-block{left:284px;top:2344px;font-size:12.5px;line-height:22px;color:#eee}
.contact-block strong{color:#fff}
.contact-line{display:flex;align-items:center;gap:10px;margin-top:16px}
.map-placeholder{left:578px;top:2346px;width:258px;height:147px;border:4px solid #fff;background:var(--placeholder)}
.footer-brand{left:914px;top:2398px;font-family:"Raleway",sans-serif;font-weight:700;font-size:24px;color:#7a7a7a;line-height:1.2;width:200px}
.bottom-bar{left:0;top:2543px;width:1200px;height:43px;background:var(--footer-deep);color:#ddd;font-size:12.5px}
.social{width:28px;height:28px;border-radius:50%;border:2px solid #fff}
</style>
</head>
<body>

<header class="site-header abs">
  <div class="brand abs"><span class="brand-dot"></span><span>Bramble Ridge Podiatry</span></div>
  <div class="topbar-phone abs">
    <svg width="14" height="14" viewBox="0 0 24 24"><path fill="#fff" d="M6.6 10.8a15 15 0 0 0 6.6 6.6l2.2-2.2c.3-.3.7-.4 1-.2 1.1.4 2.3.6 3.6.6.6 0 1 .4 1 1V20c0 .6-.4 1-1 1A17 17 0 0 1 3 4c0-.6.4-1 1-1h3.5c.6 0 1 .4 1 1 0 1.3.2 2.5.6 3.6.1.3 0 .7-.2 1z"/></svg>
    1300 555 014
  </div>
  <div class="topbar-email abs">
    <svg width="15" height="12" viewBox="0 0 24 18"><rect x="1" y="1" width="22" height="16" rx="1" fill="none" stroke="#fff" stroke-width="2"/><path d="M1 2l11 8 11-8" fill="none" stroke="#fff" stroke-width="2"/></svg>
    info@brambleridgepodiatry.net
  </div>
  <nav class="main-nav">
    <a class="active" style="left:512px">HOME</a>
    <a style="left:681px">ABOUT US</a>
    <a style="left:862px">SERVICES</a>
    <a style="left:1053px">CONTACT US</a>
  </nav>
  <span class="nav-sep abs" style="left:594px"></span>
  <span class="nav-sep abs" style="left:776px"></span>
  <span class="nav-sep abs" style="left:955px"></span>
  <span class="nav-underline abs"></span>
</header>

<section class="hero abs" role="img" aria-label="Photo of two young runners jogging along a rocky coastal path under a blue sky"></section>
<h1 class="hero-title abs">We Believe That Maintaining A Healthy<br>&amp; Active Lifestyle</h1>
<a class="btn" style="left:98px;top:417px;width:147px;height:33px">CONTACT NOW</a>

<section class="about abs"></section>
<h2 class="section-title" style="top:668px">ABOUT <span>BRAMBLE RIDGE PODIATRY</span></h2>
<div class="title-rule" style="top:721px"></div>
<div class="portrait abs" role="img" aria-label="Portrait photo of the director and chief podiatrist"></div>
<div class="about-role abs">Director / Chief Podiatrist</div>
<div class="about-name abs">Helena Marsh B.Pod. M.AHC. M.RSSFC</div>
<p class="about-bio abs">Helena graduated from Westmere University with a Bachelor of Podiatry degree in 1994. She currently holds full registration with the Foot Care Practitioners Board and the National Health Practitioner Register (NHPR). She is a full member of Active Health Council (AHC) and the Regional Society of Sports Foot Care (RSSFC). Helena has been working in various professional capacities since 1995</p>
<a class="btn" style="left:341px;top:941px;width:112px;height:35px">READ MORE</a>

<section class="services abs" role="img" aria-label="Faded background photo of a podiatrist examining a patient's foot"></section>
<h2 class="section-title" style="top:1066px">PODIATRY <span>SERVICES</span></h2>
<div class="title-rule" style="top:1119px"></div>
<p class="services-intro abs">podiatrists are trained to diagnose and treat all medical condition that affect the feet and lower limb. At Bramble Ridge Podiatry we provide treatment for<br>general &amp; Sports Podiatry conditions and various specialised treatments.</p>
<div class="tab on abs">Special Treatments</div>
<div class="tab off abs">General Treatments</div>

<span class="slider-arrow abs" style="left:64px;top:1358px">‹</span>
<span class="slider-arrow abs" style="left:1122px;top:1358px">›</span>

<div class="card-photo abs" style="left:102px;background:linear-gradient(135deg,#c98a6e,#7a4634)" role="img" aria-label="Photo of a gloved hand testing sensation on a foot"></div>
<div class="card-photo abs" style="left:357px;background:linear-gradient(135deg,#e9dfd6,#b99b86)" role="img" aria-label="Photo of toenail surgery instruments at work"></div>
<div class="card-photo abs" style="left:614px;background:linear-gradient(135deg,#5a6fa0,#c99a7c)" role="img" aria-label="Photo of a clinician assessing a patient's leg"></div>
<div class="card-photo abs" style="left:871px;background:linear-gradient(135deg,#9a7a62,#d8c5b2)" role="img" aria-label="Photo of a gloved hand treating a foot"></div>

<div class="card-title abs" style="left:102px">Diabetic<br>Management</div>
<div class="card-title abs" style="left:357px">Nail<br>Surgery</div>
<div class="card-title abs" style="left:614px">Biomechanical<br>Assessment</div>
<div class="card-title abs" style="left:871px">Gait<br>Analysis</div>

<p class="card-text abs" style="left:102px">Assessment of blood suply/circulation with doppler ultrasound; Assessment of nerve sensation via vibration</p>
<p class="card-text abs" style="left:357px">Minor surgical procedure for the permanent removal of ingrown toenails under local anaesthesia</p>
<p class="card-text abs" style="left:614px">we are able to help diagnose abnormal foot biomechanics that may be contributing to pain, injury or</p>
<p class="card-text abs" style="left:871px">Treadmill analysis of the gaint whilst walking or running to ascertain biomechanical problems or</p>

<div class="card-plus abs" style="left:204px">+</div>
<div class="card-plus abs" style="left:460px">+</div>
<div class="card-plus abs" style="left:717px">+</div>
<div class="card-plus abs" style="left:974px">+</div>

<h2 class="section-title" style="top:1704px">CLIENT <span>TESTIMONIALS</span></h2>
<div class="title-rule" style="top:1765px"></div>

<div class="round-arrow abs" style="left:45px;top:1862px">‹</div>
<div class="round-arrow abs" style="left:1125px;top:1862px">›</div>

<article class="testimonial abs" style="left:98px">
  <h3>Lorem ipsum dolor sit amet, consectet uer</h3>
  <p>Lorem ipsum dolor sit amet, consectet uer adipiscing elit, sed diam nonummy nibh euis mod tincidun nt ut laoreetml dolore magna aliquam erat volutpat.</p>
  <span class="quote-mark">”</span>
</article>
<article class="testimonial abs" style="left:615px">
  <h3>Lorem ipsum dolor sit amet, consectet uer</h3>
  <p>Lorem ipsum dolor sit amet, consectet uer adipiscing elit, sed diam nonummy nibh euis mod tincidun nt ut laoreetml dolore magna aliquam erat volutpat.</p>
  <span class="quote-mark">”</span>
</article>
<div class="tail abs" style="left:200px"></div>
<div class="tail abs" style="left:718px"></div>
<div class="avatar abs" style="left:126px" role="img" aria-label="Client portrait photo"></div>
<div class="avatar abs" style="left:643px" role="img" aria-label="Client portrait photo"></div>
<div class="client-name abs" style="left:313px">- Miss Tara Linwood<span class="stars">★★★★★</span></div>
<div class="client-name abs" style="left:800px">- Mr. Quis Nostrud Exerci<span class="stars">★★★★★</span></div>

<section class="partners abs"></section>
<div class="badge abs" style="left:288px"><i style="background:#f2c230"></i></div>
<div class="badge abs" style="left:502px"><i style="background:#3c3c3c;height:20px"></i></div>
<div class="badge abs" style="left:715px"><i style="background:#2a63b0"></i></div>
<div class="accent-rule abs"></div>

<footer class="site-footer abs"></footer>
<div class="footer-heading abs" style="left:102px">QUICK LINKS</div>
<ul class="quick-links abs">
  <li class="on">Home</li><li>About Us</li><li>Services</li><li>Contact</li>
</ul>
<span class="footer-sep abs" style="left:245px"></span>
<div class="footer-heading abs" style="left:281px">CONTACT INFORMATION</div>
<div class="contact-block abs">
  <strong>Bramble Ridge Podiatry</strong><br>Suite 12/48 Harlow<br>Street Eastvale 3000
  <div class="contact-line"><svg width="13" height="13" viewBox="0 0 24 24"><path fill="#eee" d="M6.6 10.8a15 15 0 0 0 6.6 6.6l2.2-2.2c.3-.3.7-.4 1-.2 1.1.4 2.3.6 3.6.6.6 0 1 .4 1 1V20c0 .6-.4 1-1 1A17 17 0 0 1 3 4c0-.6.4-1 1-1h3.5c.6 0 1 .4 1 1 0 1.3.2 2.5.6 3.6.1.3 0 .7-.2 1z"/></svg>1300 555 014</div>
  <div class="contact-line" style="margin-top:6px"><svg width="13" height="10" viewBox="0 0 24 18"><rect x="1" y="1" width="22" height="16" fill="none" stroke="#eee" stroke-width="2"/><path d="M1 2l11 8 11-8" fill="none" stroke="#eee" stroke-width="2"/></svg>info@brambleridgepodiatry.net</div>
</div>
<span class="footer-sep abs" style="left:548px"></span>
<div class="footer-heading abs" style="left:578px">LOCATION MAP</div>
<div class="map-placeholder abs" role="img" aria-label="Location map of the clinic"></div>
<span class="footer-sep abs" style="left:879px"></span>
<div class="footer-brand abs">Bramble Ridge Podiatry</div>

<div class="bottom-bar abs">
  <span class="abs" style="left:102px;top:13px">© 2016 Bramble Ridge Podiatry. All Rights Reserved.</span>
  <span class="abs" style="left:960px;top:13px">Follow Us :</span>
  <span class="social abs" style="left:1036px;top:8px"></span>
  <span class="social abs" style="left:1070px;top:8px"></span>
</div>

</body>
</html>
```